Wandering Rooms Stationary Set

Wandering Rooms is a bespoke interior design firm set to provide services to VIP clients with elegance and minimalism is the main theme for our stationary set. We require a full stationary set covering A4 letterhead, A4 & A3 envelopes, business cards, USB's, CDs, email signature and any other item the designer sees fit. logo is already designed and finalized, and we require the designer to use it as is without modifying the logo.

Address to be used on letterhead / business cards ...etc shall be as follows:

Phone : +971 2 518 2047
P.O. Box : 309186
Address: Block C&D, Bldg. 47, Court 12, Abu Dhabi, United Arab Emirates
Website: www.wanderingrooms-example.com

Target Market(s)

VIP Clients

Industry/Entity Type

Interior Design

Font styles to use
Other font styles liked:
• something to be unique

Colors

Designer to choose colors to be used in the design.

Requirements
Must have
• Elegant, minimalistic
Nice to have
• Simple yet elegant design having a sharp yet clean cut format
Should not have
• No additional colours, just colours that are used in the logo (silver, black or gold)

```html
<!DOCTYPE html>
<html lang="en">
<head>
<meta charset="utf-8">
<title>Wandering Rooms – Business Card</title>
<link rel="stylesheet" href="https://fonts.googleapis.com/css2?family=Cormorant+Garamond:wght@500&family=Crimson+Pro:wght@400&family=Allura&display=swap">
<style>
  :root {
    --backdrop: #1b1b1b;
    --card: #262626;
    --card-edge: #2f2f2f;
    --gold: #b59a5c;
    --gold-text: #c9a95c;
    --silver: #9a9a9a;
    --ink: #1d1d1d;
    --paper-white: #e8e8e8;
  }
  * { box-sizing: border-box; margin: 0; padding: 0; }
  html, body { width: 1200px; height: 800px; overflow: hidden; background: var(--backdrop); }
  .canvas { position: relative; width: 1200px; height: 800px; }

  .card {
    position: absolute; top: 257px; width: 500px; height: 286px;
    background: var(--card); border: 1px solid var(--card-edge); overflow: hidden;
  }
  .card--front { left: 60px; }
  .card--back { left: 640px; }

  .brand {
    position: absolute; inset: 0; display: flex; align-items: center; justify-content: center;
    font-family: "Cormorant Garamond", serif; font-weight: 500; font-size: 34px;
    letter-spacing: 0.18em; text-transform: uppercase; color: var(--silver);
  }

  .back-texture { position: absolute; inset: 0; }

  .identity {
    position: absolute; top: 44px; left: 0; right: 0; display: flex; justify-content: center;
    align-items: baseline; gap: 8px;
  }
  .identity__name { font-family: "Allura", cursive; font-size: 32px; color: var(--gold-text); }
  .identity__divider { width: 1px; height: 18px; background: var(--paper-white); align-self: center; }
  .identity__role { font-family: "Crimson Pro", serif; font-size: 17px; color: var(--paper-white); }

  .band {
    position: absolute; left: 0; right: 0; top: 92px; height: 110px; background: var(--gold);
    font-family: "Crimson Pro", serif; color: var(--ink); font-size: 12.5px; line-height: 1.3;
  }
  .band__address { position: absolute; left: 40px; bottom: 14px; }
  .band__contacts { position: absolute; right: 30px; top: 14px; list-style: none; }
  .band__contacts li { display: flex; align-items: center; gap: 7px; }
  .band__contacts svg { width: 10px; height: 10px; flex: none; }
</style>
</head>
<body>
<main class="canvas">
  <section class="card card--front">
    <p class="brand">Wandering Rooms</p>
  </section>

  <section class="card card--back">
    <svg class="back-texture" role="img" aria-label="Faint tone-on-tone brand pattern across the card back" width="500" height="286">
      <rect width="500" height="286" fill="#282828"/>
    </svg>

    <div class="identity">
      <span class="identity__name">Daniel Hayes</span>
      <span class="identity__divider"></span>
      <span class="identity__role">President</span>
    </div>

    <div class="band">
      <p class="band__address">
        P.O. Box : 309186,<br>
        Block C&amp;D, Bldg. 47, Court 12<br>
        Abu Dhabi, United Arab Emirate
      </p>
      <ul class="band__contacts">
        <li>
          <svg viewBox="0 0 10 10"><path d="M2 1l2 2-1 1.2c.6 1.2 1.5 2.1 2.8 2.8L7 6l2 2-1.3 1.3C4.5 9 1 5.5.7 2.3z" fill="var(--ink)"/></svg>
          +971 2 518 2047
        </li>
        <li>
          <svg viewBox="0 0 10 10"><rect x="0.5" y="2" width="9" height="6.5" fill="var(--ink)"/><path d="M1 2.5l4 3 4-3" stroke="var(--gold)" stroke-width="0.8" fill="none"/></svg>
          info@wanderingrooms-example.com
        </li>
        <li>
          <svg viewBox="0 0 10 10"><circle cx="5" cy="5" r="4.5" fill="var(--ink)"/><path d="M0.8 5h8.4M5 .6c-2 2.6-2 6.2 0 8.8M5 .6c2 2.6 2 6.2 0 8.8" stroke="var(--gold)" stroke-width="0.6" fill="none"/></svg>
          www.wanderingrooms-example.com
        </li>
      </ul>
    </div>
  </section>
</main>
</body>
</html>
```